Business Cards used to invite people to our church

We are a church and have need of a business card sized advertisement that allows our members to hand them out in order to invite people to the church. I need the front of the card to say "You're Invited" or "Come Check us out". with the service times on the back of the card later.
I have attached one of the OLD cards we have used in the past, but we want a complete makeover, into a more modern style that does not require the image.
I am also replacing the old logo with a newer "flat" logo which is attached.
Please use marketing colors. (blue or red or something that catches attention)
Create a card that DOES NOT have the picture of the two people on the front
The information on the sample card back is correct to go onto new card
Target Market(s)
anyone
Industry/Entity Type
Business
Contact Information for Business Card
sertice times and address information which you can get from the sample card I uploaded. It should have "You're Invited" or "Come Check us out" on the front of the card with out logo.

```html
<!DOCTYPE html>
<html lang="en">
<head>
<meta charset="utf-8">
<title>Grace Harbor – Invitation Card</title>
<link href="https://fonts.googleapis.com/css2?family=Open+Sans:wght@400;600;700&family=Parisienne&display=swap" rel="stylesheet">
<style>
  :root {
    --page-bg: #eee6d8;
    --card-center: #2c3490;
    --card-edge: #232a68;
    --ink: #ffffff;
    --ink-shadow: rgba(0, 0, 0, 0.45);
  }
  * { box-sizing: border-box; margin: 0; padding: 0; }
  html, body {
    width: 1189px;
    height: 1200px;
    overflow: hidden;
    background: var(--page-bg);
  }
  .card {
    position: absolute;
    left: 171px;
    width: 856px;
    height: 487px;
    background: radial-gradient(ellipse at 50% 55%, var(--card-center) 0%, var(--card-edge) 85%);
    color: var(--ink);
    font-family: "Open Sans", Arial, sans-serif;
    text-shadow: 1px 2px 3px var(--ink-shadow);
    text-align: center;
  }
  .card--front { top: 68px; }
  .card--back { top: 627px; }

  .church-name {
    position: absolute;
    left: 0; right: 0;
    top: 160px;
    font-weight: 700;
    font-size: 84px;
    line-height: 1;
    letter-spacing: -1px;
  }
  .tagline {
    position: absolute;
    left: 0; right: 0;
    top: 350px;
    font-family: "Parisienne", cursive;
    font-size: 58px;
    line-height: 1;
  }

  .website {
    position: absolute;
    left: 0; right: 0;
    top: 92px;
    font-weight: 600;
    font-size: 36px;
  }
  .address, .phone {
    position: absolute;
    left: 0; right: 0;
    font-size: 29px;
    font-weight: 600;
  }
  .address { top: 158px; }
  .phone { top: 196px; }

  .service-times {
    position: absolute;
    left: 122px;
    width: 612px;
    top: 274px;
    list-style: none;
    font-size: 30px;
    font-weight: 600;
  }
  .service-times li {
    display: flex;
    align-items: baseline;
    height: 42px;
  }
  .service-times .day { white-space: nowrap; }
  .service-times .leader {
    flex: 1;
    overflow: hidden;
    white-space: nowrap;
  }
  .service-times .leader::after {
    content: "................................................................................................";
  }
  .service-times .time { white-space: nowrap; }
</style>
</head>
<body>
  <section class="card card--front" aria-label="Card front">
    <h1 class="church-name">Grace Harbor</h1>
    <p class="tagline">Come Check us out</p>
  </section>

  <section class="card card--back" aria-label="Card back">
    <p class="website">GraceHarbor.org</p>
    <p class="address">2740 W. Cedar Lane - Fairview, TX 75069</p>
    <p class="phone">1-800-555-0142</p>
    <ul class="service-times">
      <li><span class="day">Sunday</span><span class="leader"></span><span class="time">9.00 AM</span></li>
      <li><span class="day">Sunday</span><span class="leader"></span><span class="time">11.00 AM</span></li>
      <li><span class="day">Wed.Bible Class</span><span class="leader"></span><span class="time">7.00 PM</span></li>
    </ul>
  </section>
</body>
</html>
```